Kelvaro.ch is looking for business card letterhead and envelope C5 with WOW effect

We need a strong business card for our company Kelvaro.ch, logo is available. You want a black or dark background on which the logo Stark r% 26 # 252; appears. Letterhead and envelope in C5 format should be in a similar design, but does not have to be We need a strong business card for our company Kelvaro.ch, logo is available. A black or dark background is desired, on which the logo Stark comes across. The letterhead and the envelope in C5 format should have a similar design.

Target Market(s)

Private customers as well as entrepreneurs

Contact Information for Business Card

E-mail: info@kelvaro-example.ch
Web.www.Kelvaro-example.ch
Tel: +41 ( 0 ) 79 482 6037
Adresse:
Lindenweg 14
9406 Tarnbach

Hier kann man Icons verwenden für Email,Tel und Adressse

Font styles to use
Other font styles liked:
• Dubai,bold

Colors

Designer to choose colors to be used in the design.

Requirements
Must have
• WOW effect
Nice to have
• R% 26 # 252; back business card with our service listings. - VEHICLE LABELING - SHOP WINDOW LABELING - STICKERS AND MUCH MORE ... in red color

```html
<!DOCTYPE html>
<html lang="en">
<head>
<meta charset="utf-8">
<title>Kelvaro.ch – Business Card</title>
<link rel="stylesheet" href="https://fonts.googleapis.com/css2?family=Lato:wght@400;700;900&display=swap">
<style>
  :root {
    --page-bg: #e9e4dc;
    --card-clear: #ddd8d0;
    --card-clear-edge: #cfc9bf;
    --panel-dark: #1c1c1e;
    --panel-dark-2: #2c2c2f;
    --gold: #c9a227;
    --gold-light: #e7c650;
    --gold-deep: #9c7a12;
    --text-muted: #b9b2a3;
    --logo-ink: #1a1a1a;
  }
  * { margin: 0; padding: 0; box-sizing: border-box; }
  html, body {
    width: 1200px;
    height: 1047px;
    overflow: hidden;
    background: var(--page-bg);
    font-family: "Lato", Arial, sans-serif;
  }
  .business-card {
    position: absolute;
    left: 100px;
    top: 251px;
    width: 1000px;
    height: 545px;
    border-radius: 22px;
    overflow: hidden;
    background: linear-gradient(160deg, #e4dfd7 0%, var(--card-clear) 60%, var(--card-clear-edge) 100%);
    box-shadow: 0 20px 50px rgba(0,0,0,0.18);
  }
  .card-shapes {
    position: absolute;
    inset: 0;
    width: 1000px;
    height: 545px;
  }
  .holder-name {
    position: absolute;
    left: 57px;
    top: 80px;
    font-size: 44px;
    font-weight: 900;
    letter-spacing: 0.5px;
    color: var(--gold);
    text-transform: uppercase;
  }
  .holder-role {
    position: absolute;
    left: 58px;
    top: 137px;
    font-size: 25px;
    color: var(--text-muted);
  }
  .address {
    position: absolute;
    left: 58px;
    top: 258px;
    font-size: 25px;
    line-height: 38px;
    color: var(--text-muted);
    font-style: normal;
  }
  .contact-list {
    position: absolute;
    left: 56px;
    top: 347px;
    list-style: none;
  }
  .contact-item {
    display: flex;
    align-items: center;
    height: 37px;
    font-size: 25px;
    color: var(--text-muted);
  }
  .contact-icon {
    width: 26px;
    height: 26px;
    margin-right: 22px;
    flex: none;
  }
  .brand {
    position: absolute;
    left: 583px;
    top: 240px;
    display: flex;
    align-items: center;
  }
  .brand-dot {
    width: 62px;
    height: 62px;
    border-radius: 50%;
    background: var(--gold);
    margin-right: 22px;
  }
  .brand-name {
    font-size: 42px;
    font-weight: 900;
    color: var(--logo-ink);
  }
</style>
</head>
<body>
  <main class="business-card">
    <svg class="card-shapes" viewBox="0 0 1000 545" aria-hidden="true">
      <defs>
        <linearGradient id="panelFill" x1="0" y1="0" x2="1" y2="1">
          <stop offset="0" stop-color="var(--panel-dark-2)"/>
          <stop offset="1" stop-color="var(--panel-dark)"/>
        </linearGradient>
        <linearGradient id="goldFill" x1="0" y1="0" x2="0" y2="1">
          <stop offset="0" stop-color="var(--gold-deep)"/>
          <stop offset="0.5" stop-color="var(--gold-light)"/>
          <stop offset="1" stop-color="var(--gold-deep)"/>
        </linearGradient>
      </defs>
      <path class="gold-sweep" d="M556,0 Q392,274 542,545 H520 Q386,274 548,0 Z" fill="url(#goldFill)"/>
      <path class="dark-panel" d="M0,0 H552 Q386,274 523,545 H0 Z" fill="url(#panelFill)"/>
    </svg>

    <h1 class="holder-name">Lena Marbach</h1>
    <p class="holder-role">Founder &amp; CEO</p>

    <address class="address">Lindenweg 14<br>9406 Tarnbach</address>

    <ul class="contact-list">
      <li class="contact-item">
        <svg class="contact-icon" viewBox="0 0 24 24" fill="none" stroke="var(--gold)" stroke-width="2" stroke-linecap="round" stroke-linejoin="round">
          <path d="M5 3h4l2 5-2.5 1.5a11 11 0 0 0 6 6L16 13l5 2v4a2 2 0 0 1-2 2A16 16 0 0 1 3 5a2 2 0 0 1 2-2z"/>
          <path d="M15 3a6 6 0 0 1 6 6M15 7a2 2 0 0 1 2 2"/>
        </svg>
        +41 ( 0 ) 79 482 6037
      </li>
      <li class="contact-item">
        <svg class="contact-icon" viewBox="0 0 24 24">
          <rect x="2" y="5" width="20" height="14" fill="var(--gold)"/>
          <path d="M2 5l10 8 10-8" fill="none" stroke="var(--panel-dark)" stroke-width="1.8"/>
        </svg>
        info@kelvaro-example.ch
      </li>
      <li class="contact-item">
        <svg class="contact-icon" viewBox="0 0 24 24" fill="none" stroke="var(--gold)" stroke-width="1.8">
          <circle cx="12" cy="12" r="9.5"/>
          <ellipse cx="12" cy="12" rx="4" ry="9.5"/>
          <path d="M2.5 12h19M4 7h16M4 17h16"/>
        </svg>
        www.Kelvaro-example.ch
      </li>
    </ul>

    <div class="brand">
      <span class="brand-dot"></span>
      <span class="brand-name">Kelvaro.ch</span>
    </div>
  </main>
</body>
</html>
```